Marwick Law Letterhead

We need a new letterhead design for a Law Firm. The address for the law firm is 1475 Calloway Street, Suite 210, Houston, Texas 77041. Phone Number: 832-361-9027; Fax Number: 832-614-7359. The logo is uploaded to the project.

```html
<!DOCTYPE html>
<html lang="en">
<head>
<meta charset="utf-8">
<title>Marwick Law Letterhead</title>
<link href="https://fonts.googleapis.com/css2?family=Arimo:wght@400;700&display=swap" rel="stylesheet">
<style>
  :root {
    --bg: #ececec;
    --paper: #fbfbfb;
    --navy: #1f2a5c;
    --red: #c8202f;
    --ink: #3a3a3a;
    --muted: #555;
  }
  * { box-sizing: border-box; margin: 0; padding: 0; }
  html, body { width: 1200px; height: 795px; overflow: hidden; }
  body {
    background: var(--bg);
    font-family: "Arimo", Arial, sans-serif;
    color: var(--ink);
    position: relative;
  }
  .letterhead {
    position: absolute;
    left: 331px; top: 18px;
    width: 538px; height: 760px;
    background: var(--paper);
    box-shadow: 0 2px 10px rgba(0,0,0,.12);
  }
  .brand {
    position: absolute; left: 58px; top: 58px;
    display: flex; align-items: center; gap: 8px;
  }
  .brand-dot { width: 22px; height: 22px; border-radius: 50%; background: var(--navy); }
  .brand-name {
    font-size: 19px; font-weight: 700; color: var(--navy); letter-spacing: .5px;
  }
  .letter-body {
    position: absolute; left: 58px; top: 200px; width: 420px;
    font-size: 8.4px; line-height: 1.45; color: var(--muted);
  }
  .salutation { font-size: 11px; color: var(--ink); margin-bottom: 10px; }
  .letter-body p { margin-bottom: 12px; }
  .closing { margin-top: 16px; font-size: 8.4px; }
  .signature {
    display: block; margin-top: 6px; width: 90px; height: 34px;
    background: #e4e4e4;
  }
  .footer {
    position: absolute; left: 58px; right: 42px; bottom: 42px;
  }
  .rule { height: 1px; }
  .rule-red { background: var(--red); }
  .rule-navy { background: var(--navy); }
  .contact {
    display: flex; align-items: center; gap: 4px;
    font-size: 9.6px; color: #111; padding: 7px 0;
  }
  .contact svg { width: 9px; height: 9px; fill: var(--red); flex: none; }
  .contact .sep { width: 6px; }
</style>
</head>
<body>
  <main class="letterhead">
    <header class="brand">
      <span class="brand-dot"></span>
      <span class="brand-name">Marwick Law</span>
    </header>

    <section class="letter-body">
      <div class="salutation">Dear Mr. Smith,</div>
      <p>Lorem ipsum dolor sit amet, consectetur adipiscing elit. Donec orci purus, luctus vitae dignissim eu, iaculis sed purus. Vivamus faucibus, ipsum nec aliquet viverra, leo mauris condimentum ligula, sit amet sagittis enim ligula quis arcu. Nam egestas tortor id nisl porttitor mattis. In tortor ante, ultricies in suscipit a, tempus non massa. Vivamus et auctor mi. Fusce vel massa nulla. Phasellus nec eros mauris, et scelerisque orci.</p>
      <p>Donec malesuada orci vitae nulla accumsan porta a id massa. Quisque accumsan iaculis magna sit amet fringilla. Maecenas consequat, magna eget tincidunt semper, odio nibh rutrum mi, id feugiat ante nisl eu risus. Vestibulum nunc orci, rhoncus a placerat in, ultricies in mi. Cras mattis varius eros, vel fringilla nisi suscipit eget. Quisque scelerisque sagittis nulla at porttitor.</p>
      <p>Sed id augue vitae urna euismod commodo aliquet a quam. Pellentesque arcu velit, cursus et malesuada ut, consequat et diam. Nullam erat sem, rhoncus id ullamcorper vitae, rhoncus et arcu. In ultricies ultricies nulla, ut rutrum nisl iaculis at. Donec eu magna a metus ornare faucibus. Fusce aliquet faucibus ultricies. Morbi semper, est id tincidunt gravida, sem arcu adipiscing lacus, ac bibendum nulla leo eu purus. Quisque nec diam sed risus consectetur accumsan quis quis nibh. Vestibulum id purus lorem.</p>
      <div class="closing">Sincerely,
        <span class="signature" role="img" aria-label="Handwritten signature"></span>
      </div>
    </section>

    <footer class="footer">
      <div class="rule rule-red"></div>
      <div class="contact">
        <svg viewBox="0 0 10 10" aria-hidden="true"><path d="M5 0a3.5 3.5 0 0 0-3.5 3.5C1.5 6 5 10 5 10s3.5-4 3.5-6.5A3.5 3.5 0 0 0 5 0zm0 5a1.5 1.5 0 1 1 0-3 1.5 1.5 0 0 1 0 3z"/></svg>
        <span>1475 Calloway Street, Suite 210, Houston, Texas 77041</span>
        <span class="sep"></span>
        <svg viewBox="0 0 10 10" aria-hidden="true"><path d="M2 0l2 2.5-1 1.2a6 6 0 0 0 3.3 3.3l1.2-1L10 8l-1.5 2C4 10 0 6 0 1.5z"/></svg>
        <span>832-361-9027</span>
        <span class="sep"></span>
        <svg viewBox="0 0 10 10" aria-hidden="true"><path d="M2.5 0h5v3h-5zM0 3.5h10V8H8v2H2V8H0zm3 3V9h4V6.5z"/></svg>
        <span>832-614-7359.</span>
      </div>
      <div class="rule rule-navy"></div>
    </footer>
  </main>
</body>
</html>
```